The quiet harbor with an elephant incorporated in the background

Target Market(s)

Real estate

Industry/Entity Type

Real Estate

Contact Information for Business Card

On back on want my name & number
In front I want the business name, "the quiet harbor", below to say staging & design

Logo Text

The quiet harbor

Font styles to use
Serif

Colors
000000

Requirements
Must have
• I want an elephant behind the writing in gold transperant

```html
<!DOCTYPE html>
<html lang="en">
<head>
<meta charset="utf-8">
<title>The Quiet Harbor – Business Card</title>
<link rel="stylesheet" href="https://fonts.googleapis.com/css2?family=Questrial&family=Open+Sans:wght@400;700&display=swap">
<style>
  :root {
    --backdrop: #7f7f7f;
    --card-dark: #120808;
    --card-dark-2: #1a0f0f;
    --gold: #e0b418;
    --rule: #6e6457;
    --muted: #9a928a;
    --white: #f4f1ec;
  }
  * { margin: 0; padding: 0; box-sizing: border-box; }
  html, body { width: 1200px; height: 900px; overflow: hidden; }
  body {
    background: var(--backdrop);
    font-family: "Questrial", "Century Gothic", sans-serif;
    position: relative;
  }
  .card {
    position: absolute;
    top: 306px;
    width: 439px;
    height: 271px;
    border-radius: 10px;
    overflow: hidden;
    background: var(--card-dark);
  }
  .card-front { left: 149px; }
  .card-back { left: 609px; background: var(--card-dark-2); }

  .elephant-watermark {
    position: absolute;
    left: 6px; top: 4px;
    width: 282px; height: 267px;
    border-radius: 46% 40% 8% 8% / 40% 40% 6% 6%;
    background: radial-gradient(ellipse at 50% 55%, rgba(224,180,24,0.16), rgba(224,180,24,0.09) 55%, rgba(224,180,24,0.03) 85%);
  }
  .accent-band {
    position: absolute;
    right: 0; top: 0;
    width: 90px; height: 100%;
    background: var(--gold);
  }
  .band-disc {
    position: absolute;
    left: 288px; top: 48px;
    width: 112px; height: 154px;
    border-radius: 50%;
    background: var(--card-dark);
  }

  .wordmark {
    position: absolute;
    text-align: center;
    color: var(--gold);
  }
  .wordmark .lead {
    display: flex; align-items: center; justify-content: center; gap: 8px;
    font-size: 14px; letter-spacing: 0.5px; line-height: 1;
  }
  .wordmark .lead::before, .wordmark .lead::after,
  .wordmark .tagline::before, .wordmark .tagline::after {
    content: ""; height: 1px; background: var(--rule); flex: 1;
  }
  .wordmark .name {
    font-size: 26px; line-height: 1.3; letter-spacing: 0.3px; white-space: nowrap;
  }
  .wordmark .tagline {
    display: flex; align-items: center; gap: 6px;
    color: var(--muted); font-size: 11px; letter-spacing: 0.5px; line-height: 1;
  }
  .card-front .wordmark { left: 33px; top: 49px; width: 216px; }
  .card-back .wordmark { left: 99px; top: 162px; width: 240px; }
  .card-back .wordmark .name { font-size: 29px; line-height: 1.3; }
  .card-back .wordmark .lead { font-size: 15px; }
  .card-back .wordmark .tagline { font-size: 12px; }

  .person-name {
    position: absolute; left: 24px; top: 147px;
    font-family: "Open Sans", Arial, sans-serif; font-weight: 700;
    font-size: 16px; color: var(--gold); letter-spacing: 0.2px;
  }
  .contact-list {
    position: absolute; left: 26px; top: 210px;
    list-style: none;
    font-family: "Open Sans", Arial, sans-serif; font-size: 13px; color: var(--white);
  }
  .contact-list li { display: flex; align-items: center; gap: 8px; height: 19px; }
  .contact-list svg { width: 13px; height: 13px; fill: var(--gold); }

  .pattern-field {
    position: absolute; inset: 0;
    background: linear-gradient(180deg, #1d1212, #170d0d);
  }
  .brand-disc {
    position: absolute; left: 182px; top: 50px;
    width: 76px; height: 76px; border-radius: 50%;
    background: var(--gold);
  }
</style>
</head>
<body>
  <section class="card card-front">
    <div class="elephant-watermark" role="img" aria-label="Transparent gold elephant silhouette behind the writing"></div>
    <div class="accent-band"></div>
    <div class="band-disc"></div>
    <div class="wordmark">
      <div class="lead">THE</div>
      <div class="name">QUIET HARBOR</div>
      <div class="tagline">STAGING &amp; DESIGN</div>
    </div>
    <p class="person-name">DANIEL REYES</p>
    <ul class="contact-list">
      <li>
        <svg viewBox="0 0 24 24" aria-hidden="true"><path d="M6.6 10.8a15.1 15.1 0 0 0 6.6 6.6l2.2-2.2a1 1 0 0 1 1-.25 11.4 11.4 0 0 0 3.6.57 1 1 0 0 1 1 1V20a1 1 0 0 1-1 1A17 17 0 0 1 3 4a1 1 0 0 1 1-1h3.5a1 1 0 0 1 1 1c0 1.25.2 2.45.57 3.6a1 1 0 0 1-.25 1z"/></svg>
        (044)987654321
      </li>
      <li>
        <svg viewBox="0 0 24 24" aria-hidden="true"><path d="M2 5h20v14H2z M2 5l10 8 10-8" /></svg>
        hello@quietharbor.com
      </li>
    </ul>
  </section>

  <section class="card card-back">
    <div class="pattern-field" role="img" aria-label="Subtle dark repeating pattern background"></div>
    <div class="brand-disc"></div>
    <div class="wordmark">
      <div class="lead">THE</div>
      <div class="name">QUIET HARBOR</div>
      <div class="tagline">STAGING &amp; DESIGN</div>
    </div>
  </section>
</body>
</html>
```